Poster for a Bicycle show/Expo

We need a poster for a Bicycle show/Expo and sustainable transport. Exhibitors will sell bikes, cycling clothing, accessories, etc. ...
This show is annual and the Poster is for the 2015 edition.

The style must be modern, dynamic, bright colors.

Your concept must be compatible in a landscape format. (We will ourselves adaptations of different formats.)
Width: 210 mm
Height: 297 mm
It's necessary for us to have the source file (vector) for make, later, the different format (flyers, website, ...)

Content of the Poster:
- 1 big picture (no clip art)
- Big title: « Foire du Rayon » (« Salon » or « Salon du » can be small and « Vélo » big.)
- Subtitle: « et de la mobilité douce »
- Date: « 8, 9 et 10 mai 2015 » or « 8-10 mai 2015 »
- Place: « Halle TRV - Gare de Lunel »
- Text line 1: « www.foire-du-rayon.ch - Entrée gratuite »
- Text line 2« Piste d’essais - Restauration sur place »
- Text line 3: « Ve 8 mai de 17h à 21h - Sa 9 mai de 10h à 20h - Di 10 mai de 10h à 18h »
- Please, leave a zone in the poster for sponsors logos
(The predominant information (most visible) are: « Foire du Rayon » and « 8, 9 et 10 mai 2015 or 8-10 mai 2015 »)

Content of the big picture:
- from a cheap stock, like PixKiosk.com
- a bicycle in action or a detail of a bicycle (or a accessory) (no race bike)
- a modern picture with bright colors.
- if a person is on the picture, we prefer a men
- not an aerial view with cyclists in a landscape.

Some examples of poster of shows - with typo-title worked

http://www.expobassinlutece.com/Temp/IMG/F_a9b3c2d4e5f60718293a4b5c6d7e8f9012345678901_200_296.png

http://qx4m.tornafoire.fr/Data/pvtorn_mer/block/F_7cc1bb9396aef1d5e69283647561f0076457c357c5ea6.pdf
(page 2 of this PDF)

http://salons.rivol-evenements.fr/images/rivol-evenements/foires-salons/phototheque/salon-auto-bourlac/salon-auto-bourlac2012-affiche.jpg

http://www.tirovel.net/blog/wp-content/uploads/2007/03/affiche-salon-du-livre.jpg

http://www.quaimarin-gens.com/wp-content/affiche-cannes-2007.jpg
Updates

Hello,

For information, for your next versions, please, add the text "Piste d'essais".

- Text line 1: « www.foire-du-rayon.ch - Entrée gratuite »
- Text line 2: « Piste d’essais - Restauration sur place »
- Text line 3: « Ve 8 mai de 17h à 21h - Sa 9 mai de 10h à 20h - Di 10 mai de 10h à 18h »

Thanks,
Rodolphe

```html
<!DOCTYPE html>
<html lang="fr">
<head>
<meta charset="utf-8">
<title>Foire du Rayon 2015</title>
<link rel="stylesheet" href="https://fonts.googleapis.com/css2?family=Michroma&family=Roboto+Condensed:wght@400&family=Lato:wght@400&display=swap">
<style>
  :root {
    --banner-red: #c8141f;
    --banner-red-dark: #8e0c14;
    --band-dark: #1c1c1e;
    --band-grey: #3a3a3c;
    --info-grey: #d3d3d5;
    --date-yellow: #f4e01f;
    --text-white: #ffffff;
    --text-dark: #1e1e1e;
    --sponsor-grey: #7a7a7a;
    --page: #ffffff;
  }
  * { margin: 0; padding: 0; box-sizing: border-box; }
  html, body { width: 842px; height: 1200px; overflow: hidden; background: var(--page); }
  .poster { position: relative; width: 842px; height: 1200px; background: var(--page); overflow: hidden; }
  .hero-photo {
    position: absolute; left: 0; top: 0; width: 842px; height: 858px;
    background:
      linear-gradient(180deg, rgba(235,235,230,0.9) 0%, rgba(235,235,230,0) 22%),
      linear-gradient(160deg, #5d6a3c 0%, #3f4b2a 30%, #7a6a3a 48%, #8b8f88 62%, #6e716e 100%);
  }
  .title-art { position: absolute; left: 0; top: 0; width: 842px; height: 858px; }
  .title-main, .title-sub, .event-date { font-family: "Michroma", sans-serif; }
  .title-main { font-size: 54px; fill: var(--text-white); }
  .title-sub { font-size: 30px; fill: var(--text-white); }
  .event-date { font-size: 30px; fill: var(--date-yellow); }
  .event-place { font-family: "Roboto Condensed", sans-serif; font-size: 27px; fill: var(--text-white); letter-spacing: 0.5px; }
  .info-band {
    position: absolute; left: 0; top: 858px; width: 842px; height: 128px;
    background: var(--info-grey);
    font-family: "Roboto Condensed", sans-serif; color: var(--text-dark);
    font-size: 24px; text-align: center;
  }
  .info-line { position: absolute; left: 0; right: 0; white-space: nowrap; }
  .info-line--web { top: 26px; display: flex; justify-content: center; align-items: center; gap: 6px; }
  .info-line--hours { top: 68px; }
  .globe-icon { width: 22px; height: 22px; }
  .info-rule {
    position: absolute; left: 0; top: 986px; width: 842px; height: 5px;
    background: linear-gradient(90deg, #222 0%, #222 40%, #bbb 65%, #222 100%);
  }
  .sponsor-zone { position: absolute; left: 0; top: 991px; width: 842px; height: 195px; }
  .sponsor-label {
    position: absolute; left: 0; right: 0; bottom: 32px; text-align: center;
    font-family: "Lato", sans-serif; font-size: 18px; color: var(--sponsor-grey);
  }
  .footer-bar {
    position: absolute; left: 0; top: 1186px; width: 842px; height: 14px;
    background: linear-gradient(180deg, var(--banner-red) 0%, var(--banner-red-dark) 100%);
  }
</style>
</head>
<body>
<div class="poster">
  <div class="hero-photo" role="img" aria-label="Photo: three road cyclists in bright blue, yellow and red jackets riding on a mountain road lined with autumn forest"></div>

  <svg class="title-art" viewBox="0 0 842 858" aria-hidden="false">
    <defs>
      <linearGradient id="redBanner" x1="0" y1="0" x2="1" y2="0">
        <stop offset="0" stop-color="#e01b25"/>
        <stop offset="1" stop-color="#8e0c14"/>
      </linearGradient>
      <linearGradient id="darkBand" x1="0" y1="0" x2="0" y2="1">
        <stop offset="0" stop-color="#4a4a4c"/>
        <stop offset="0.5" stop-color="#262628"/>
        <stop offset="1" stop-color="#151516"/>
      </linearGradient>
      <linearGradient id="silverFold" x1="0" y1="0" x2="1" y2="1">
        <stop offset="0" stop-color="#ffffff"/>
        <stop offset="0.5" stop-color="#9a9a9a"/>
        <stop offset="1" stop-color="#3a3a3a"/>
      </linearGradient>
    </defs>
    <polygon class="band-dark" points="267,761 842,678 842,858 324,858" fill="url(#darkBand)"/>
    <polygon class="banner-red" points="165,608 842,516 842,669 156,757" fill="url(#redBanner)"/>
    <polygon class="banner-fold" points="156,757 272,761 302,849" fill="url(#silverFold)"/>
    <g transform="rotate(-7.5 208 669)">
      <text class="title-main" x="208" y="669" textLength="570" lengthAdjust="spacingAndGlyphs">Foire du Rayon</text>
      <line x1="208" y1="684" x2="792" y2="684" stroke="#3a0508" stroke-width="1.5"/>
      <line x1="208" y1="686" x2="792" y2="686" stroke="#e86068" stroke-width="1"/>
      <text class="title-sub" x="212" y="727" textLength="572" lengthAdjust="spacingAndGlyphs">et de la mobilité douce</text>
    </g>
    <text class="event-date" x="792" y="781" text-anchor="end" textLength="406" lengthAdjust="spacingAndGlyphs">8, 9 et 10 mai 2015</text>
    <text class="event-place" x="792" y="821" text-anchor="end">Halle TRV - Gare de Lunel</text>
  </svg>

  <div class="info-band">
    <p class="info-line info-line--web">
      <svg class="globe-icon" viewBox="0 0 24 24" fill="none" stroke="#1e1e1e" stroke-width="1.4">
        <circle cx="12" cy="12" r="10"/>
        <ellipse cx="12" cy="12" rx="4.5" ry="10"/>
        <line x1="2" y1="12" x2="22" y2="12"/>
        <path d="M4 7h16M4 17h16"/>
      </svg>
      <span>www.foire-du-rayon.ch - Entrée gratuite - Restauration sur place</span>
    </p>
    <p class="info-line info-line--hours">Ve 8 mai de 17h à 21h - Sa 9 mai de 10h à 20h - Di 10 mai de 10h à 18h</p>
  </div>
  <div class="info-rule"></div>

  <div class="sponsor-zone">
    <p class="sponsor-label">sponsors logos</p>
  </div>
  <div class="footer-bar"></div>
</div>
</body>
</html>
```